I need a website designed. I am a mortgage loan officer and would like to have a website for me and my team where i can post resources, videos and blog information for my clients. A website like themorvaskteam.com .

The theme is - The Pelkins Team - Home Loan Group powered by Brightwell Home Loans -

Target Market(s)

B2B (Real Estate Agents)and B2C (Home buyers and refinancing)

Industry/Entity Type

Mortgage Lender

Coding

Coded - Design and coding required

Number of Pages Required

5+ page

Font styles to use
Serif
Sans Serif

Colors

Designer to choose colors to be used in the design.

Requirements
Must have
• Disclaimers: Licensed by the Bureau of Lending Affairs under the Pacific Credit Providers Act. Loans made or arranged pursuant to a Pacific Credit Providers Act License. Equal Housing Lender Brightwell Cannot Accept mortgage applications for properties located in New York via this site
• Mobile Friendly
Nice to have
• Main Links: Home, About Us(see team flyer), Mortgage 101, Contact Us (formzig form)

```html
<!DOCTYPE html>
<html lang="en">
<head>
<meta charset="utf-8">
<title>The Pelkins Team – Home Loan Group</title>
<link rel="stylesheet" href="https://fonts.googleapis.com/css2?family=Raleway:wght@500;600;700;800&family=Open+Sans:ital,wght@0,400;0,600;0,700;1,400&display=swap">
<style>
:root{
  --blue:#2196e8;
  --ink:#222;
  --text:#555;
  --muted:#888;
  --rule:#d9d9d9;
  --footer:#8d8d8d;
  --white:#fff;
  --card-tint:#f1f6fb;
}
*{box-sizing:border-box;margin:0;padding:0}
html,body{width:1200px;height:3758px;overflow:hidden}
body{position:relative;font-family:"Open Sans",Arial,sans-serif;color:var(--text);background:var(--white)}
.abs{position:absolute}
h1,h2,h3,h4,.brand{font-family:"Raleway","Open Sans",sans-serif}

/* Hero */
.hero{left:0;top:0;width:1200px;height:580px;background:linear-gradient(180deg,#4f6f93 0%,#7f97b3 35%,#8c8f86 60%,#4f6b3a 85%,#3d5a2c 100%)}
.hero-shade{left:0;top:0;width:1200px;height:580px;background:linear-gradient(180deg,rgba(10,25,45,.55),rgba(0,0,0,.05) 45%,rgba(0,0,0,.15))}
.brand{left:84px;top:30px;width:320px;color:var(--white);text-align:center}
.brand-mark{display:block;width:44px;height:44px;margin:0 auto 10px;background:var(--white)}
.brand-name{font-size:30px;font-weight:700;letter-spacing:.3px;line-height:1;white-space:nowrap}
.brand-sub{font-size:17px;font-weight:600;letter-spacing:2px;margin-top:8px;white-space:nowrap;display:flex;align-items:center;gap:8px;justify-content:center}
.brand-sub::before,.brand-sub::after{content:"";width:22px;height:2px;background:var(--white)}
.nav{top:52px;right:95px;display:flex;gap:34px;align-items:center;font-family:"Raleway",sans-serif;font-size:15px;font-weight:700;color:var(--white)}
.nav .active{color:#3ab0ff}
.hero-title{left:0;width:1200px;top:225px;text-align:center;color:var(--white);font-size:58px;font-weight:800;letter-spacing:.5px}
.hero-sub{left:0;width:1200px;top:303px;text-align:center;color:var(--white);font-size:27px}
.hero-btn{left:508px;top:362px;width:184px;height:48px;background:var(--blue);color:var(--white);font-family:"Raleway",sans-serif;font-weight:700;font-size:15px;display:flex;align-items:center;justify-content:center;letter-spacing:.5px}
.dots{left:570px;top:510px;display:flex;gap:6px}
.dots span{width:13px;height:13px;border-radius:50%;border:2px solid var(--white)}
.dots span.on{background:var(--white)}

/* About */
.portrait{left:78px;top:635px;width:362px;height:362px;border-radius:50%;background:radial-gradient(circle at 50% 40%,#d7c0ad,#8b7a6e 60%,#3a3f52);border:8px solid var(--white);box-shadow:0 0 0 2px #ddd,0 4px 14px rgba(0,0,0,.2)}
.arrow{left:398px;top:930px}
.signature{left:505px;top:930px;width:210px;height:46px;background:linear-gradient(90deg,#e6e6e6,#f3f3f3)}
.about-name{left:505px;top:665px;font-size:30px;font-weight:700;color:var(--ink);letter-spacing:.5px}
.about-role{left:505px;top:708px;font-size:17px;font-weight:600;color:var(--blue)}
.about-text{left:505px;top:755px;width:595px;font-size:13.6px;line-height:24px;color:var(--text)}
.rule{left:100px;width:1000px;height:1px;background:var(--rule)}

.sec-title{left:0;width:1200px;text-align:center;font-size:31px;font-weight:700;color:var(--ink);letter-spacing:.5px}

/* Videos */
.video{top:1198px;width:315px;height:190px}
.video .thumb{width:100%;height:100%}
.play{position:absolute;left:50%;top:50%;width:46px;height:46px;margin:-23px 0 0 -23px}
.video-cap{position:absolute;top:205px;left:0;width:100%;text-align:center;font-size:17px;font-weight:600;color:var(--ink)}

/* Team */
.team{left:0;top:1512px;width:1200px;height:575px;background:linear-gradient(180deg,rgba(45,145,230,.88),rgba(55,155,232,.92)),linear-gradient(90deg,#9cc4e8,#d8e6f2 50%,#9cc4e8)}
.team .sec-title{top:58px;color:var(--white)}
.member{top:217px;width:278px;height:285px;background:var(--white);text-align:center}
.avatar{position:absolute;left:50%;top:-85px;width:188px;height:188px;margin-left:-94px;border-radius:50%;border:5px solid var(--white);background:radial-gradient(circle at 50% 38%,#c9a88f,#6f5a4f 55%,#2d2f3a);box-shadow:0 2px 8px rgba(0,0,0,.3)}
.member-body{position:absolute;top:122px;left:0;width:100%;padding:0 22px;display:flex;flex-direction:column;align-items:center}
.member-name{font-size:16px;font-weight:700;color:var(--ink);margin-bottom:6px}
.member-info{font-size:13px;line-height:21px;color:var(--text)}
.member-more{display:block;margin-top:10px}

/* Blog */
.blog-feature{left:100px;top:2245px;width:435px;height:390px;background:var(--card-tint)}
.blog-feature .thumb{width:435px;height:218px;background:linear-gradient(135deg,#a9b5c2,#e7e1d8 50%,#b4848a)}
.post-title{font-size:18px;font-weight:700;color:var(--ink);font-family:"Raleway",sans-serif}
.post-meta{font-size:11.5px;color:var(--muted);display:flex;gap:12px;align-items:center;margin-top:8px}
.post-meta span{display:flex;align-items:center;gap:5px}
.post-text{font-size:13.5px;line-height:21px;color:var(--text);margin-top:8px}
.read-more{font-size:12.5px;font-weight:700;color:var(--blue);font-family:"Raleway",sans-serif;margin-top:14px;letter-spacing:.3px}
.blog-feature .body{padding:18px 32px}
.blog-side{left:568px;width:532px;height:170px}
.blog-side .thumb{position:absolute;left:0;top:0;width:168px;height:170px}
.blog-side .body{position:absolute;left:202px;top:0;width:330px}

/* Resources */
.resource{top:2858px;width:322px}
.resource .thumb{width:100%;height:207px}
.resource .post-title{margin-top:32px}

/* Footer */
.footer{left:0;top:3335px;width:1200px;height:423px;background:var(--footer)}
.footer-brand{left:0;width:1200px;top:52px;display:flex;justify-content:center;align-items:center;gap:16px;color:var(--white)}
.footer-brand .sq{width:74px;height:74px;border:3px solid var(--white)}
.footer-brand .name{font-family:"Raleway",sans-serif;font-weight:600;font-size:38px;line-height:1.05;letter-spacing:3px}
.contact-row{top:165px;left:245px;display:flex;align-items:center;color:var(--white);font-size:13.5px}
.contact-item{display:flex;align-items:center;gap:18px;margin-right:62px}
.icon-circle{width:44px;height:44px;border-radius:50%;border:2px solid var(--white);display:flex;align-items:center;justify-content:center}
.foot-links{left:0;width:1200px;top:233px;display:flex;justify-content:center;gap:22px;color:var(--white);font-size:14px}
.foot-rule{left:100px;top:272px;width:1000px;height:1px;background:rgba(255,255,255,.45)}
.copyright{left:100px;top:300px;font-size:12.5px;color:var(--white)}
.disclaimer{left:100px;top:333px;width:760px;font-size:11.3px;line-height:22px;color:var(--white);font-style:italic}
.social{top:287px;right:100px;display:flex;gap:10px}
.social span{width:34px;height:34px;border-radius:50%;border:2px solid var(--white)}
</style>
</head>
<body>

<header class="abs hero" role="img" aria-label="Photo of a large two-storey suburban house with a green front lawn under a blue sky"></header>
<div class="abs hero-shade"></div>
<div class="abs brand"><span class="brand-mark"></span><div class="brand-name">THE PELKINS TEAM</div><div class="brand-sub">HOME LOAN GROUP</div></div>
<nav class="abs nav">
  <span class="active">HOME</span><span>ABOUT US</span><span>MORTGAGE 101</span><span>CONTACT US</span>
  <svg width="16" height="16" viewBox="0 0 16 16" fill="none" stroke="#fff" stroke-width="2.4"><circle cx="6.5" cy="6.5" r="5"/><path d="M10.5 10.5L15 15"/></svg>
</nav>
<h1 class="abs hero-title">THE PELKINS TEAM</h1>
<p class="abs hero-sub">We are a home loan company</p>
<div class="abs hero-btn">CALL US TODAY</div>
<div class="abs dots"><span class="on"></span><span></span><span></span><span></span></div>

<section>
  <div class="abs portrait" role="img" aria-label="Portrait photo of Ivan Pelkins"></div>
  <svg class="abs arrow" width="100" height="60" viewBox="0 0 100 60" fill="none" stroke="#666" stroke-width="3" stroke-linecap="round"><path d="M95 40 C70 55 40 50 12 22"/><path d="M12 22 L14 40 M12 22 L30 24"/></svg>
  <div class="abs signature" role="img" aria-label="Handwritten signature of Ivan Pelkins"></div>
  <h2 class="abs about-name">IVAN PELKINS</h2>
  <p class="abs about-role">Producing Branch Manager</p>
  <p class="abs about-text">I have over 15 years of experience in Mortgage Planning. I rank in the top 1% of loan originators in the country. I pride myself on making the home buying process as smooth as possible. I will guide you through the mortgage process and look forward to helping you with your transaction. My team has been awarded with the Circle of Excellence award and CEO Club for being in the top 5 teams in the country having helped over 700+ families achieve the dream of home ownership between the years 2016 and 2017 and counting.</p>
</section>
<div class="abs rule" style="top:1068px"></div>

<h2 class="abs sec-title" style="top:1124px">VIDEOS</h2>
<div class="abs video" style="left:100px"><div class="thumb" role="img" aria-label="Video still of a small house model beside a pen and contract" style="background:linear-gradient(135deg,#f2f2f2,#d9d9d9 60%,#b9a79a)"></div>
  <svg class="play" viewBox="0 0 46 46"><circle cx="23" cy="23" r="21" fill="rgba(0,0,0,.55)" stroke="#fff" stroke-width="2"/><path d="M18 14 L32 23 L18 32Z" fill="#fff"/></svg>
  <div class="video-cap">Finibus Bono Malorum</div></div>
<div class="abs video" style="left:443px"><div class="thumb" role="img" aria-label="Video still of a family using a laptop at home" style="background:linear-gradient(135deg,#e9dccb,#b59b82 55%,#7d6a5c)"></div>
  <svg class="play" viewBox="0 0 46 46"><circle cx="23" cy="23" r="21" fill="rgba(0,0,0,.55)" stroke="#fff" stroke-width="2"/><path d="M18 14 L32 23 L18 32Z" fill="#fff"/></svg>
  <div class="video-cap">Finibus Bono Malorum</div></div>
<div class="abs video" style="left:786px"><div class="thumb" style="background:#000"></div>
  <svg class="play" viewBox="0 0 46 46"><circle cx="23" cy="23" r="21" fill="rgba(0,0,0,.55)" stroke="#fff" stroke-width="2"/><path d="M18 14 L32 23 L18 32Z" fill="#fff"/></svg>
  <div class="video-cap">Finibus Bono Malorum</div></div>

<section class="abs team" role="img" aria-label="Blue-tinted photo of a family inside a bright new home">
  <h2 class="abs sec-title">TEAM MEMBERS</h2>
  <div class="abs member" style="left:100px">
    <div class="avatar" role="img" aria-label="Portrait photo of Marco Ellison"></div>
    <div class="member-body"><div class="member-name">MARCO ELLISON</div>
      <div class="member-info">Loan Partner I - NMLS ID: 1730815<br>Marco.Ellison@brightwellhomeloans.com<br>(555) 014-7202</div>
      <svg class="member-more" width="18" height="18" viewBox="0 0 18 18"><circle cx="9" cy="9" r="9" fill="#2196e8"/><path d="M9 5v8M5 9h8" stroke="#fff" stroke-width="2"/></svg></div>
  </div>
  <div class="abs member" style="left:461px">
    <div class="avatar" role="img" aria-label="Portrait photo of Dario Quint"></div>
    <div class="member-body"><div class="member-name">DARIO QUINT</div>
      <div class="member-info">Loan Processor – NMLS ID: 1582240<br>Dario.Quint@brightwellhomeloans.com<br>(555) 018-9294</div>
      <svg class="member-more" width="18" height="18" viewBox="0 0 18 18"><circle cx="9" cy="9" r="9" fill="#2196e8"/><path d="M9 5v8M5 9h8" stroke="#fff" stroke-width="2"/></svg></div>
  </div>
  <div class="abs member" style="left:822px">
    <div class="avatar" role="img" aria-label="Portrait photo of Helena Marsh" style="background:radial-gradient(circle at 50% 38%,#e8cfb4,#c9a46c 55%,#2d2f3a)"></div>
    <div class="member-body"><div class="member-name">HELENA MARSH</div>
      <div class="member-info">Closing Coordinator/Team<br>Leader–NMLS 1460937<br>Helena.Marsh@brightwellhomeloans.com<br>(555) 012-1151</div>
      <svg class="member-more" width="18" height="18" viewBox="0 0 18 18" style="margin-top:4px"><circle cx="9" cy="9" r="9" fill="#2196e8"/><path d="M9 5v8M5 9h8" stroke="#fff" stroke-width="2"/></svg></div>
  </div>
</section>

<h2 class="abs sec-title" style="top:2160px">LATEST BLOG</h2>
<article class="abs blog-feature">
  <div class="thumb" role="img" aria-label="Photo of a couple meeting an advisor on a sofa"></div>
  <div class="body">
    <h3 class="post-title">Finibus Bonorum et Malorum</h3>
    <div class="post-meta"><span><svg width="11" height="11" viewBox="0 0 11 11"><rect x="0.5" y="1.5" width="10" height="9" fill="none" stroke="#2196e8"/><path d="M0.5 4h10" stroke="#2196e8"/></svg>28/12/2017</span><span><svg width="10" height="11" viewBox="0 0 10 11" fill="#2196e8"><circle cx="5" cy="3" r="2.6"/><path d="M0 11c0-3.5 2.3-5 5-5s5 1.5 5 5z"/></svg>John Doe</span></div>
    <p class="post-text">Nam libero tempore, cum soluta nobis est eligendi optio cumque nihil impedit quo minus id...</p>
    <div class="read-more">READ MORE</div>
  </div>
</article>
<article class="abs blog-side" style="top:2250px">
  <div class="thumb" role="img" aria-label="Photo of a woman reading documents" style="background:linear-gradient(135deg,#a36d4a,#e3c6a6 55%,#d9d2c8)"></div>
  <div class="body"><h3 class="post-title">At vero eos et accusamus et iui</h3>
    <div class="post-meta"><span><svg width="11" height="11" viewBox="0 0 11 11"><rect x="0.5" y="1.5" width="10" height="9" fill="none" stroke="#2196e8"/><path d="M0.5 4h10" stroke="#2196e8"/></svg>28/12/2017</span><span><svg width="10" height="11" viewBox="0 0 10 11" fill="#2196e8"><circle cx="5" cy="3" r="2.6"/><path d="M0 11c0-3.5 2.3-5 5-5s5 1.5 5 5z"/></svg>John Doe</span></div>
    <p class="post-text">Nam libero tempore, cum soluta nobis est eligendi optio cumque nihil impedit...</p>
    <div class="read-more">READ MORE</div></div>
</article>
<article class="abs blog-side" style="top:2465px">
  <div class="thumb" role="img" aria-label="Photo of a couple reviewing papers together" style="background:linear-gradient(135deg,#dfe6ea,#b7a08c 55%,#6b8a9a)"></div>
  <div class="body"><h3 class="post-title">At vero eos et accusamus et iui</h3>
    <div class="post-meta"><span><svg width="11" height="11" viewBox="0 0 11 11"><rect x="0.5" y="1.5" width="10" height="9" fill="none" stroke="#2196e8"/><path d="M0.5 4h10" stroke="#2196e8"/></svg>28/12/2017</span><span><svg width="10" height="11" viewBox="0 0 10 11" fill="#2196e8"><circle cx="5" cy="3" r="2.6"/><path d="M0 11c0-3.5 2.3-5 5-5s5 1.5 5 5z"/></svg>John Doe</span></div>
    <p class="post-text">Nam libero tempore, cum soluta nobis est eligendi optio cumque nihil impedit...</p>
    <div class="read-more">READ MORE</div></div>
</article>
<div class="abs rule" style="top:2718px"></div>

<h2 class="abs sec-title" style="top:2778px">RESOURCES</h2>
<article class="abs resource" style="left:100px">
  <div class="thumb" role="img" aria-label="Photo of a modern house under a blue sky" style="background:linear-gradient(180deg,#3c83c9,#a9c7e2 50%,#7a8a74)"></div>
  <h3 class="post-title">Finibus Bonorum et Malorum</h3>
  <div class="post-meta"><span><svg width="11" height="11" viewBox="0 0 11 11"><rect x="0.5" y="1.5" width="10" height="9" fill="none" stroke="#2196e8"/><path d="M0.5 4h10" stroke="#2196e8"/></svg>25/09/2017</span><span><svg width="10" height="11" viewBox="0 0 10 11" fill="#2196e8"><circle cx="5" cy="3" r="2.6"/><path d="M0 11c0-3.5 2.3-5 5-5s5 1.5 5 5z"/></svg>John</span></div>
  <p class="post-text">Nemo enim ipsam voluptatem quia volupta asperna tur aut odit aut fugit, sed quia conseq.</p>
  <div class="read-more">READ MORE</div>
</article>
<article class="abs resource" style="left:438px">
  <div class="thumb" role="img" aria-label="Photo of a couple meeting a loan advisor at a desk" style="background:linear-gradient(135deg,#c98b63,#e5d2bf 50%,#8c6a55)"></div>
  <h3 class="post-title">Finibus Bonorum et Malorum</h3>
  <div class="post-meta"><span><svg width="11" height="11" viewBox="0 0 11 11"><rect x="0.5" y="1.5" width="10" height="9" fill="none" stroke="#2196e8"/><path d="M0.5 4h10" stroke="#2196e8"/></svg>25/09/2017</span><span><svg width="10" height="11" viewBox="0 0 10 11" fill="#2196e8"><circle cx="5" cy="3" r="2.6"/><path d="M0 11c0-3.5 2.3-5 5-5s5 1.5 5 5z"/></svg>John</span></div>
  <p class="post-text">Nemo enim ipsam voluptatem quia volupta asperna tur aut odit aut fugit, sed quia conseq.</p>
  <div class="read-more">READ MORE</div>
</article>
<article class="abs resource" style="left:777px">
  <div class="thumb" role="img" aria-label="Photo of hands with a calculator and paperwork" style="background:linear-gradient(135deg,#f4f4f4,#d6d6d6 55%,#a9a9a9)"></div>
  <h3 class="post-title">Finibus Bonorum et Malorum</h3>
  <div class="post-meta"><span><svg width="11" height="11" viewBox="0 0 11 11"><rect x="0.5" y="1.5" width="10" height="9" fill="none" stroke="#2196e8"/><path d="M0.5 4h10" stroke="#2196e8"/></svg>25/09/2017</span><span><svg width="10" height="11" viewBox="0 0 10 11" fill="#2196e8"><circle cx="5" cy="3" r="2.6"/><path d="M0 11c0-3.5 2.3-5 5-5s5 1.5 5 5z"/></svg>John</span></div>
  <p class="post-text">Nemo enim ipsam voluptatem quia volupta asperna tur aut odit aut fugit, sed quia conseq.</p>
  <div class="read-more">READ MORE</div>
</article>

<footer class="abs footer">
  <div class="abs footer-brand"><span class="sq"></span><div class="name">BRIGHTWELL<br>HOME LOANS</div></div>
  <div class="abs contact-row">
    <div class="contact-item"><span class="icon-circle"><svg width="16" height="20" viewBox="0 0 16 20" fill="#fff"><path d="M8 0a8 8 0 0 0-8 8c0 6 8 12 8 12s8-6 8-12a8 8 0 0 0-8-8zm0 11a3 3 0 1 1 0-6 3 3 0 0 1 0 6z"/></svg></span><span>4120 Alder Creek Rd, Suite 310,<br>Lakeview FL 30001</span></div>
    <div class="contact-item"><span class="icon-circle"><svg width="18" height="18" viewBox="0 0 18 18" fill="#fff"><path d="M3.6 0.8 6.4 4c.5.6.4 1.4-.1 1.9L5 7.2c1 2.2 3.5 4.8 5.8 5.8l1.3-1.3c.5-.5 1.3-.6 1.9-.1l3.2 2.8c.6.5.6 1.4 0 2l-1.4 1.4C13.4 19.2 0-2 3.6.8z"/></svg></span><span>1-555-014-7202</span></div>
    <div class="contact-item"><span class="icon-circle"><svg width="18" height="13" viewBox="0 0 18 13"><rect x="0.8" y="0.8" width="16.4" height="11.4" fill="#fff"/><path d="M1 1l8 6 8-6" fill="none" stroke="#8d8d8d" stroke-width="1.5"/></svg></span><span>info@thepelkinsteam.com</span></div>
  </div>
  <div class="abs foot-links"><span>Home</span><span>|</span><span>About us</span><span>|</span><span>Mortgage 101</span><span>|</span><span>Contact us</span></div>
  <div class="abs foot-rule"></div>
  <p class="abs copyright">Copyrights © 2018, The Pelkins Team. All rights reserved.</p>
  <p class="abs disclaimer">Licensed by the Bureau of Lending Affairs under the Pacific Credit Providers Act. Loans made or arranged pursuant to a Pacific Credit Providers Act License. Equal Housing Lender Brightwell Cannot Accept mortgage applications for properties located in New York via this site.</p>
  <div class="abs social"><span></span><span></span><span></span></div>
</footer>

</body>
</html>
```